Dwelvano - "Where Pest Control is Free for Life..." Please see pitch deck...

Project goal, that this is a reusable template, not a one-off card
Brand and design direction, follow the logo, use the brand palette (with a color swatch table), typography and layout guidance
The John Doe placeholder content as a clean field-by-field table (name, title, company, address, office, cell, fax, email, dwelvano.com)
Print specs, 3.5 × 2 in trim, 0.125 in bleed, 300 DPI, CMYK, crop marks
Deliverables, layered editable PSD (your primary ask) plus vector .AI/.EPS and a press-ready PDF/X-1a, with fonts packaged
What you'll provide (logo, colors, fonts)
Process and sign-off, concept first, then full file package on approval.
Populate every field with this John Doe placeholder data so we can see the layout fully built out. We will replace it per person.
Name John Doe
Title Title / Position
Company Dwelvano
Address 123 Main Street, Suite 100, Tallahassee, FL 32301
Office (850) 555-0100
Cell (850) 555-0123
Fax (850) 555-0199
Email johndoe@dwelvano.com
Website dwelvano.com

We need the working, editable source files so we can update them ourselves, plus a ready-to-print export:
1. Photoshop (.PSD) — fully layered and editable, with each contact field on its own labeled text layer. This is the primary requested format.
2. Vector source — the press-standard editable format, Adobe Illustrator (.AI) and/or .EPS, since vector is preferred for crisp text and logos at print.
3. Print-ready PDF — press-quality (PDF/X-1a), CMYK, with bleed and crop marks, both sides.
4. Packaged fonts and links — include or list all fonts used, and package any linked assets so the files open correctly on our end.

Why both PSD and vector
The PSD covers our request directly and is easy for us to edit. Vector (.AI/.EPS) is what most commercial printers actually prefer for type and logos because it stays razor-sharp at any size. Providing both keeps us flexible no matter which printer we use. Have fun and keep it modern and cool the designer of the logo did a great job, see what you can do.

```html
<!DOCTYPE html>
<html lang="en">
<head>
<meta charset="utf-8">
<title>Dwelvano Business Card – Front and Back</title>
<link rel="stylesheet" href="https://fonts.googleapis.com/css2?family=Poppins:wght@300;400;600;700&display=swap">
<style>
  :root {
    --stage: #5e5e5e;
    --navy: #0a1226;
    --navy-deep: #070d1c;
    --teal: #06b4c6;
    --teal-soft: #0b6f82;
    --white: #ffffff;
  }
  * { box-sizing: border-box; margin: 0; padding: 0; }
  html, body {
    width: 1200px; height: 800px; overflow: hidden;
    background: var(--stage);
    font-family: "Poppins", sans-serif;
  }
  .stage { position: relative; width: 1200px; height: 800px; }
  .card {
    position: absolute; width: 560px; height: 320px;
    background: var(--navy-deep);
    overflow: hidden;
    box-shadow: 0 14px 30px rgba(0,0,0,0.45);
  }
  .card--front { left: 20px; top: 140px; }
  .card--back  { left: 620px; top: 340px; }

  /* Front side */
  .pattern-field {
    position: absolute; inset: 0;
    background:
      radial-gradient(ellipse at 95% 0%, rgba(6,180,198,0.55) 0%, rgba(11,111,130,0.25) 35%, rgba(10,18,38,0) 70%),
      var(--navy);
  }
  .front-wordmark {
    position: absolute; right: 60px; top: 150px;
    color: var(--white); font-weight: 700; font-size: 24px; letter-spacing: -0.3px;
  }

  /* Back side */
  .brand { position: absolute; left: 36px; top: 136px; width: 262px; }
  .brand__name {
    color: var(--white); font-weight: 700; font-size: 48px; line-height: 1; letter-spacing: -1px;
  }
  .brand__tagline {
    margin-top: 8px;
    color: var(--white); font-weight: 700; font-size: 10px; letter-spacing: 0.5px; text-transform: uppercase;
    white-space: nowrap;
  }
  .brand__subline {
    margin-top: 1px;
    color: var(--teal); font-weight: 300; font-size: 10px;
  }
  .divider {
    position: absolute; left: 312px; top: 56px; width: 1px; height: 156px;
    background: var(--teal);
  }
  .person { position: absolute; left: 332px; top: 50px; }
  .person__name {
    font-size: 28px; line-height: 1.1; color: var(--white); font-weight: 300;
  }
  .person__first { color: var(--teal); font-weight: 700; }
  .person__title {
    color: var(--white); font-weight: 600; font-size: 12px; margin-top: 2px;
  }
  .contacts { list-style: none; margin-top: 10px; }
  .contacts li {
    display: flex; align-items: center; gap: 8px;
    color: var(--white); font-size: 11px; font-weight: 400; line-height: 17px;
  }
  .contacts svg { width: 11px; height: 11px; flex: none; }
  .address-band {
    position: absolute; left: 0; top: 238px; width: 472px; height: 30px;
    background: var(--teal);
    display: flex; align-items: center; padding-left: 140px;
    color: var(--white); font-size: 12.5px; font-weight: 400; white-space: nowrap;
  }
  .band-block {
    position: absolute; left: 472px; top: 222px; width: 46px; height: 46px;
    background: var(--teal);
  }
  .band-tab {
    position: absolute; left: 518px; top: 222px; width: 42px; height: 22px;
    background: var(--white);
  }
</style>
</head>
<body>
<main class="stage">

  <section class="card card--front" aria-label="Card front">
    <div class="pattern-field" role="img" aria-label="Repeating brand pattern in teal fading into navy"></div>
    <p class="front-wordmark">dwelvano.com</p>
  </section>

  <section class="card card--back" aria-label="Card back">
    <div class="brand">
      <p class="brand__name">Dwelvano</p>
      <p class="brand__tagline">Caring for the homes you love</p>
      <p class="brand__subline">A friendlier home service</p>
    </div>

    <div class="divider"></div>

    <div class="person">
      <p class="person__name"><span class="person__first">John</span> Doe</p>
      <p class="person__title">Title / Position</p>
      <ul class="contacts">
        <li>
          <svg viewBox="0 0 24 24" fill="var(--teal)" aria-hidden="true"><path d="M6.6 10.8a15 15 0 0 0 6.6 6.6l2.2-2.2a1 1 0 0 1 1-.25 11.4 11.4 0 0 0 3.6.57 1 1 0 0 1 1 1V20a1 1 0 0 1-1 1A17 17 0 0 1 3 4a1 1 0 0 1 1-1h3.5a1 1 0 0 1 1 1 11.4 11.4 0 0 0 .57 3.6 1 1 0 0 1-.25 1z"/></svg>
          (850) 555-0100
        </li>
        <li>
          <svg viewBox="0 0 24 24" fill="none" stroke="var(--teal)" stroke-width="2" aria-hidden="true"><rect x="6" y="2" width="12" height="20" rx="2"/><line x1="11" y1="18" x2="13" y2="18"/></svg>
          (850) 555-0123
        </li>
        <li>
          <svg viewBox="0 0 24 24" fill="var(--teal)" aria-hidden="true"><rect x="6" y="2" width="12" height="7"/><rect x="2" y="9" width="20" height="11" rx="2"/><rect x="7" y="13" width="10" height="2" fill="var(--navy-deep)"/></svg>
          (850) 555-0199
        </li>
        <li>
          <svg viewBox="0 0 24 24" fill="none" stroke="var(--teal)" stroke-width="2" aria-hidden="true"><circle cx="12" cy="12" r="10"/><path d="M2 12h20M12 2a15 15 0 0 1 0 20M12 2a15 15 0 0 0 0 20"/></svg>
          www.dwelvano.com
        </li>
        <li>
          <svg viewBox="0 0 24 24" fill="none" stroke="var(--teal)" stroke-width="2" aria-hidden="true"><rect x="2" y="5" width="20" height="14" rx="1"/><path d="M2 6l10 7 10-7"/></svg>
          johndoe@dwelvano.com
        </li>
      </ul>
    </div>

    <div class="address-band">123 Main Street, Suite 100, Tallahassee, FL 32301</div>
    <div class="band-block"></div>
    <div class="band-tab"></div>
  </section>

</main>
</body>
</html>
```